Marlowe Crest Realty business card design

Looking for an upscale and clean business card design and updated logo. I sell to a very high-end south Florida real estate market.
Target Market(s)
High-end real estate in south Florida real estate market
Industry/Entity Type
Real Estate Agent
Contact Information for Business Card
Marlowe Crest Realty, Inc
738 West Pinecrest Ave, Suite 410/510, Fort Lauderdale, FL 33308
Gary Whitlock - Broker/Owner
954-327-8846 Direct
garyshomes@quellmail.com
Website: DwellTarrowBay.com
Font styles to use
Other font styles liked:
- Copperplate Gothic, Georgia, etc.
Requirements
Must have
- My photo, company name, my name and title, all info stated in Details above
Nice to have
- Luxury home design element, waterfront

```html
<!DOCTYPE html>
<html lang="en">
<head>
<meta charset="utf-8">
<title>Marlowe Crest Realty – Business Card</title>
<link rel="stylesheet" href="https://fonts.googleapis.com/css2?family=Alegreya:wght@700&family=Cormorant+Garamond:wght@500&family=Questrial&display=swap">
<style>
  :root {
    --ink: #141414;
    --paper: #ffffff;
    --gold: #f5c52e;
    --stage: #2a2a2a;
    --photo: #c9c9c9;
    --rule: #bdbdbd;
    --text: #1a1a1a;
  }
  * { box-sizing: border-box; margin: 0; padding: 0; }
  html, body { width: 1200px; height: 866px; overflow: hidden; }
  body {
    background: var(--stage);
    display: flex; align-items: center; justify-content: center; gap: 40px;
  }
  .card {
    position: relative; width: 540px; height: 309px; overflow: hidden;
    border-radius: 3px; box-shadow: 0 10px 24px rgba(0,0,0,.45);
  }
  /* Front */
  .card--front { background: var(--paper); }
  .front-band { position: absolute; inset: 0; width: 100%; height: 100%; }
  .photo {
    position: absolute; left: 30px; top: 38px; width: 214px; height: 148px;
    border-radius: 14px; background: linear-gradient(180deg, var(--photo), #b7b7b7);
  }
  .identity { position: absolute; left: 30px; top: 208px; }
  .identity__name {
    font-family: "Alegreya", Georgia, serif; font-weight: 700;
    font-size: 30px; color: var(--gold); line-height: 1;
  }
  .identity__title {
    font-family: "Questrial", Arial, sans-serif; font-size: 15px;
    color: var(--paper); margin-top: 6px;
  }
  .contact {
    position: absolute; left: 282px; top: 66px; width: 240px;
    font-family: "Questrial", Arial, sans-serif; color: var(--text);
    font-size: 13px; line-height: 1.35;
  }
  .contact__rule { border: 0; border-top: 1px solid var(--rule); margin: 8px 0 8px; width: 210px; }
  .contact__line { display: flex; align-items: center; gap: 7px; }
  .contact__icon { width: 13px; height: 13px; flex: none; }
  /* Back */
  .card--back {
    background: var(--ink);
    display: flex; align-items: center; justify-content: center; gap: 16px;
  }
  .brand__dot { width: 30px; height: 30px; border-radius: 50%; background: var(--gold); }
  .brand__name {
    font-family: "Cormorant Garamond", Georgia, serif; font-weight: 500;
    font-size: 30px; letter-spacing: 1.5px; color: var(--paper); line-height: 1.15;
  }
</style>
</head>
<body>
  <section class="card card--front">
    <svg class="front-band" viewBox="0 0 540 309" aria-hidden="true">
      <polygon points="0,182 282,182 300,309 0,309" fill="var(--ink)"/>
    </svg>
    <div class="photo" role="img" aria-label="Portrait photo of Gary Whitlock"></div>
    <div class="identity">
      <p class="identity__name">Gary Whitlock</p>
      <p class="identity__title">Broker/Owner</p>
    </div>
    <div class="contact">
      <p>738 West Pinecrest Ave</p>
      <p>Suite 410/510</p>
      <p>Fort Lauderdale, FL 33308</p>
      <hr class="contact__rule">
      <p class="contact__line">
        <svg class="contact__icon" viewBox="0 0 16 16" aria-hidden="true"><path d="M4 1l3 3-2 2c1 2 3 4 5 5l2-2 3 3-2 2C7 14 2 9 2 3z" fill="var(--gold)"/></svg>
        954-327-8846 Direct
      </p>
      <p class="contact__line">
        <svg class="contact__icon" viewBox="0 0 16 16" aria-hidden="true"><rect x="1" y="3" width="14" height="10" fill="var(--gold)"/><path d="M1 3l7 6 7-6" stroke="var(--paper)" stroke-width="1.3" fill="none"/></svg>
        garyshomes@quellmail.com
      </p>
      <p class="contact__line">
        <svg class="contact__icon" viewBox="0 0 16 16" aria-hidden="true"><g fill="none" stroke="var(--gold)" stroke-width="1.4"><circle cx="8" cy="8" r="6.5"/><ellipse cx="8" cy="8" rx="3" ry="6.5"/><path d="M1.5 8h13M3 4.5h10M3 11.5h10"/></g></svg>
        www.DwellTarrowBay.com
      </p>
    </div>
  </section>

  <section class="card card--back">
    <span class="brand__dot" aria-hidden="true"></span>
    <p class="brand__name">Marlowe Crest<br>Realty, Inc.</p>
  </section>
</body>
</html>
```